Creative UI design for web application

I need a new UI design for my web application. It will be used by small and micro business owners to plan & implement growth tactics.

I've attached the current design (which I'm open to be changed) - but in particular I need to design the centre of the screen, where the work actually happens.

There needs to be place for a title (YOUR BUSINESS) and description (say 1-2 paragraphs of text) - and am happy to include icons or imagery where makes sense. It may make sense for the user to be able to upload their business logo and name, for example.

This screen will be used by the business owner to understand the real value they offer potential customers and their point of difference - why they exist and why potential customers should care.

They'll use the information they put into this screen to plan things like their messaging.

Following that, there needs to be 2 sections in the dashboard.

The first section is titled "WHO YOU ARE"

The first section will include a number of boxes that the user can input information into, as follows:

- Logo
- Business name
- Business tag line
- Business vision
- Business bio
- Brand colours (these should end up as swatches based on the colour code they enter) - the colour code for each colour swatch should also be visible.
- Key competitors
- SWOT analysis (boxes to enter their strengths, weaknesses, opportunities and threats).

The second section is titled "WHY YOU EXIST"

The second section will include a number of boxes that the user can input information (text) into, as follows:

- Who are your ideal customers?
- What problem are you trying to solve for them?
- What pain points will this remove for them?
- How do you solve it?
- How else could this problem be solved?
- Who offers these other solutions?
- Why is your solution better?
- How much does your solution cost?
- What value are you providing to justify this cost?
- How will this make their life/job easier/better?

They should be able to write a decent amount of information in the boxes.

There should ideally be a place for a description for each of these text fields (for both section 1 & 2) as well so I can give them a little bit more direction around what to put in the box. Alternatively there could be a little icon (say a question mark or "i") that they could click on to view instructions. The instructions will be around 2-4 sentences long for each text field.

You have 2 options:

a) This all needs to appear on the one screen, and the navigation needs to be visible (as per the example attached but feel free to recreate this navigation)

Note: the page can scroll below the fold - but please provide the design for the full length of the page.

b) Potentially the 2 sections could actually be in 2 different items in the menu - YOUR BUSINESS and YOUR VALUE (which would sit next to YOUR BUSINESS and before YOUR CUSTOMER in the screenshot provided). feel free to design them as 2 separate screens if you prefer.

I have attached a screenshot of the app as it stands today (screen shot 2017) which would still exist in the new design but under a different section (the learn section from the plan2 mockup attached)

I have mocked up how this new screen could look if broken into 2 and that's also attached. If you can make this come to life - and look more engaging that would be helpful! :)

Target Market(s)

Small and micro business owners

Industry/Entity Type

Marketing

Number of Pages Required

1 page

Font styles to use
Sans Serif
Other font styles liked:
• Montserrat

Colors
87cfc6
d2a4cc
ffffff
85cae6
e8e8e8
5c5c5c

Requirements
Must have
• Use of my brand colours: #cc8eb2, #76d6c8, #68c7ff as well as white and #595959. Must be visually pleasing / engaging, designed for desktop (as it's a desktop application), really easy to use / navigate.
• Use font Montserrat light & Montserrat Regular or Bold. Mostly should be Montserrat light.
Nice to have
• Would be nice to see how this would look on mobile (as the application is responsive) but this is not mandatory.
Should not have
• Should not look too corporate or dry.

```html
<!DOCTYPE html>
<html lang="en">
<head>
<meta charset="utf-8">
<title>Leafline – Your Business</title>
<link rel="stylesheet" href="https://fonts.googleapis.com/css2?family=Montserrat:wght@300;400;600;700&display=swap">
<style>
:root{
  --nav-dark:#3b3b3b;
  --teal:#76d6c8;
  --teal-deep:#4fbfae;
  --pink:#cc8eb2;
  --pink-deep:#a5579a;
  --sky-top:#86cbe7;
  --sky-bottom:#1596d0;
  --grey-bar:#e8e8e8;
  --text:#595959;
  --text-soft:#8a8a8a;
  --line:#e3e3e3;
  --white:#ffffff;
}
*{box-sizing:border-box;margin:0;padding:0}
html,body{width:1200px;height:3098px;overflow:hidden}
body{font-family:"Montserrat",sans-serif;font-weight:300;color:var(--text);background:var(--white);position:relative}
.abs{position:absolute}

/* top navigation */
.topbar{left:0;top:0;width:1200px;height:60px;background:var(--nav-dark);border-top:4px solid var(--teal)}
.topbar .tab{position:absolute;top:0;height:56px;line-height:56px;font-size:15px;color:#fff;font-weight:400}
.topbar .tab.active{left:37px;width:114px;background:var(--teal);text-align:center}
.brand{left:0;right:0;text-align:center;top:20px;font-size:19px;letter-spacing:.5px;color:#fff;font-weight:600}
.brand span{font-weight:300}
.account{top:18px;font-size:14px;color:#fff;display:flex;align-items:center;gap:8px;font-weight:400}

/* sub navigation */
.subnav{left:0;top:60px;width:1200px;height:54px;background:var(--grey-bar)}
.subnav a{position:absolute;top:18px;font-size:14px;color:var(--text);text-decoration:none;font-weight:400}
.subnav a.current{color:var(--pink)}
.subnav .underline{position:absolute;left:58px;top:46px;width:134px;height:6px;background:var(--pink)}

/* intro */
.company-card{left:37px;top:173px;width:671px;height:106px;border:1px solid var(--line);display:flex}
.company-card .mark{width:246px;border-right:1px solid var(--line);display:flex;align-items:center;justify-content:center;gap:10px;font-size:24px;font-weight:700;color:#2e2e2e}
.company-card .mark i{width:20px;height:20px;background:#2e2e2e;display:block}
.company-card .info{padding:18px 20px}
.company-card h1{font-size:25px;font-weight:700;color:#2e2e2e;letter-spacing:.5px}
.contacts{display:flex;gap:22px;margin-top:12px;font-size:13px;font-weight:400;color:#333;align-items:center}
.contacts span{display:flex;align-items:center;gap:8px}
.intro-lead{left:37px;top:296px;width:671px;font-size:13px;line-height:21px;font-weight:400;text-transform:uppercase;color:#444}
.intro-text{left:37px;width:671px;font-size:11.5px;line-height:23px;color:var(--text-soft)}
.photo-frame{left:739px;top:173px;width:422px;height:341px;border:1px solid var(--line);padding:14px}
.photo-frame div{width:100%;height:100%;background:linear-gradient(135deg,#d7dde3,#8c9aa8 55%,#4a5767)}

/* who you are */
.who{left:0;top:578px;width:1200px;height:1037px;background:linear-gradient(180deg,var(--sky-top),var(--sky-bottom))}
.section-title{position:absolute;left:0;width:1200px;text-align:center;font-size:24px;font-weight:600;letter-spacing:1px}
.who .section-title{top:56px;color:#fff}
.field{position:absolute;border:1px solid rgba(255,255,255,.7);color:#fff;font-size:11.5px;line-height:22px}
.field .label{margin:6px;height:31px;background:#fff;color:var(--pink);font-size:14px;padding:0 14px;line-height:31px;display:flex;justify-content:space-between;align-items:center}
.field p{padding:4px 18px}
.info-dot{width:12px;height:12px;border-radius:50%;background:var(--pink);color:#fff;font-size:9px;line-height:12px;text-align:center;font-weight:700}
.swatches{display:flex;gap:32px;padding:8px 28px}
.swatches .group{display:flex;gap:2px}
.swatches .group b{width:29px;height:29px;border-radius:50%;display:block;border:2px solid rgba(255,255,255,.9)}
.swot{position:absolute;left:609px;width:552px;border:1px solid rgba(255,255,255,.7);color:#fff;font-size:11.5px;padding:0 16px;line-height:44px}

/* why you exist */
.why .section-title{top:1674px;color:#2e2e2e}
.qcard{position:absolute;border:1px solid var(--line);font-size:11.5px;line-height:23px;color:#555}
.qcard .head{margin:6px;height:30px;background:linear-gradient(180deg,#c58abd,var(--pink-deep));color:#fff;font-size:14px;padding:0 14px;display:flex;justify-content:space-between;align-items:center}
.qcard .head .info-dot{background:#fff;color:var(--pink-deep)}
.qcard p{padding:8px 20px}
.save{left:991px;top:2940px;width:170px;height:46px;background:linear-gradient(180deg,#8fe0d4,var(--teal-deep));color:#fff;font-weight:700;font-size:13px;text-align:center;line-height:46px;letter-spacing:.5px}
.footer{left:0;top:3021px;width:1200px;height:77px;background:#575757;color:#fff;font-size:11px;font-weight:400}
.footer .copy{position:absolute;left:0;width:1200px;text-align:center;top:31px}
.footer .code{position:absolute;right:40px;top:31px}
</style>
</head>
<body>

<header class="abs topbar">
  <div class="tab active">Plan</div>
  <div class="tab" style="left:216px">Learn</div>
  <div class="tab" style="left:362px">Remember</div>
  <div class="abs brand">LEAF<span>LINE</span></div>
  <div class="abs account" style="left:968px">
    <svg width="18" height="18" viewBox="0 0 18 18"><circle cx="9" cy="9" r="8" fill="none" stroke="#76d6c8" stroke-width="1.6"/><circle cx="9" cy="7" r="3" fill="#76d6c8"/><path d="M3.5 14.5c1.5-3 9.5-3 11 0" fill="#76d6c8"/></svg>My Profile</div>
  <div class="abs account" style="left:1090px">
    <svg width="16" height="16" viewBox="0 0 16 16"><rect x="1" y="2" width="8" height="12" fill="none" stroke="#76d6c8" stroke-width="1.6"/><path d="M6 8h9M12 5l3 3-3 3" fill="none" stroke="#76d6c8" stroke-width="1.6"/></svg>Log out</div>
</header>

<nav class="abs subnav">
  <a class="current" style="left:70px">Your Business</a>
  <a style="left:290px">Your Products</a>
  <a style="left:512px">Your Customers</a>
  <a style="left:746px">Your Goals</a>
  <a style="left:946px">Your Plan</a>
  <div class="underline"></div>
</nav>

<section>
  <div class="abs company-card">
    <div class="mark"><i></i>Northfield</div>
    <div class="info">
      <h1>NORTHFIELD STUDIO</h1>
      <div class="contacts">
        <span><svg width="30" height="30" viewBox="0 0 30 30"><circle cx="15" cy="15" r="14" fill="none" stroke="#cc8eb2" stroke-width="1.5"/><path d="M11 9l3 3-2 2c1 2 2 3 4 4l2-2 3 3-2 2c-5 0-10-5-10-10z" fill="#cc8eb2"/></svg>Contact : +1.555.010.2040</span>
        <span><svg width="30" height="30" viewBox="0 0 30 30"><circle cx="15" cy="15" r="14" fill="none" stroke="#cc8eb2" stroke-width="1.5"/><rect x="9" y="10" width="12" height="10" fill="#cc8eb2"/><path d="M9 10l6 5 6-5" fill="none" stroke="#fff" stroke-width="1.2"/></svg>hello@northfield.studio</span>
      </div>
    </div>
  </div>
  <p class="abs intro-lead">Aliquip ex ea commodo consequat. Duis aute irure dolor in reprehenderit excepteur cupidatat non proident culpa qui officia laboris nisi...</p>
  <p class="abs intro-text" style="top:344px">Explorer of the truth, the master-builder of human happiness. No one rejects, dislikes, or avoids pleasure itself, because it is pleasure, but because those who do not know how to pursue pleasure rationally encounter consequences that are extremely painful. Nor again is there anyone who loves or pursues or desires to obtain pain of itself, because it is pain, but because...</p>
  <p class="abs intro-text" style="top:428px">Explorer of the truth, the master-builder of human happiness. No one rejects, dislikes, or avoids pleasure itself, because it is pleasure, but because those who do not know how to pursue pleasure rationally encounter consequences that are extremely painful. Nor again is there anyone who loves or pursues or desires to obtain pain of itself, because it is pain, but because placeat facere possimus, omnis voluptas assumenda est, omnis dolor repellendus. Temporibus autem quibusdam...</p>
  <div class="abs photo-frame"><div role="img" aria-label="Photo of two business people reviewing a tablet at a desk"></div></div>
</section>

<section class="abs who">
  <h2 class="section-title">WHO YOU ARE</h2>
  <div class="field" style="left:37px;top:141px;width:368px;height:103px"><div class="label">Logo</div><p>Upload Your Company Logo Here</p></div>
  <div class="field" style="left:421px;top:141px;width:362px;height:103px"><div class="label">Business Name</div><p>Write Your Company Name</p></div>
  <div class="field" style="left:799px;top:141px;width:362px;height:103px"><div class="label">Business tag line</div><p>Explain the value of your business in 5 words or less</p></div>
  <div class="field" style="left:37px;top:260px;width:368px;height:232px"><div class="label">Business vision<span class="info-dot">i</span></div><p>What do you want to achieve in the next 12 months? Think about this from your customer's perspective. What problem are you trying to solve? What is your vision for solving this problem?</p></div>
  <div class="field" style="left:421px;top:260px;width:740px;height:232px"><div class="label">Business Bio<span class="info-dot">i</span></div><p>What are you? What do you do? This is the type of information that you'd have on the "about"<br>page of your Website</p></div>
  <div class="field" style="left:37px;top:508px;width:1124px;height:104px"><div class="label">Brand colours<span class="info-dot">i</span></div>
    <div class="swatches">
      <div class="group"><b style="background:#1a7fb8"></b><b style="background:#1ea7d6"></b><b style="background:#6fd0ea"></b><b style="background:#c7eef8"></b></div>
      <div class="group"><b style="background:#a3142a"></b><b style="background:#d42c3d"></b><b style="background:#ec8d97"></b><b style="background:#f6cfd3"></b></div>
      <div class="group"><b style="background:#f2a71c"></b><b style="background:#f6c547"></b><b style="background:#f8da84"></b><b style="background:#fbecc2"></b></div>
      <div class="group"><b style="background:#1e3f8a"></b><b style="background:#4867b4"></b><b style="background:#8fa3d6"></b><b style="background:#d3dcf0"></b></div>
      <div class="group"><b style="background:#2a8a3a"></b><b style="background:#4caf59"></b><b style="background:#8dcf96"></b><b style="background:#d0ecd4"></b></div>
    </div>
  </div>
  <div class="field" style="left:37px;top:628px;width:554px;height:318px"><div class="label">Key competitors<span class="info-dot">i</span></div><p>Ducimus qui blanditiis praesentium voluptatum deleniti atque corrupti quos<br>dolores et quas molestias excepturi sint occaecati ?</p></div>
  <div class="field" style="left:609px;top:628px;width:552px;height:107px"><div class="label">SWOT analysis<span class="info-dot">i</span></div><p>Ducimus qui blanditiis praesentium voluptatum deleniti atque corrupti quos<br>dolores et quas molestias excepturi sint occaecati ?</p></div>
  <div class="swot" style="top:746px;height:45px">Enter Strengths</div>
  <div class="swot" style="top:799px;height:46px">Enter Weaknesses</div>
  <div class="swot" style="top:851px;height:45px">Enter Opportunities</div>
  <div class="swot" style="top:903px;height:45px">Enter Threats</div>
</section>

<section class="why">
  <h2 class="section-title">WHY YOU EXIST</h2>
  <div class="qcard" style="left:37px;top:1730px;width:554px;height:228px"><div class="head">Who are your ideal customers?<span class="info-dot">i</span></div><p>Ducimus qui blanditiis praesentium voluptatum deleniti atque corrupti quos<br>dolores et quas molestias excepturi sint occaecati ?</p></div>
  <div class="qcard" style="left:609px;top:1730px;width:552px;height:228px"><div class="head">What problem are you trying to solve for them?<span class="info-dot">i</span></div><p>Ducimus qui blanditiis praesentium voluptatum deleniti atque corrupti quos dolores et quas molestias excepturi sint occaecati praesentium voluptatum deleniti atque cupiditate non provident, similique?</p></div>
  <div class="qcard" style="left:37px;top:1987px;width:554px;height:121px"><div class="head">How do you solve it?<span class="info-dot">i</span></div><p>Ducimus qui blanditiis praesentium voluptatum deleniti?</p></div>
  <div class="qcard" style="left:609px;top:1987px;width:552px;height:421px"><div class="head">What pain points will this remove for them?<span class="info-dot">i</span></div><p>Ducimus qui blanditiis praesentium voluptatum deleniti atque corrupti quos dolores et quas molestias excepturi sint occaecati praesentium voluptatum deleniti atque cupiditate non provident, similique?</p></div>
  <div class="qcard" style="left:37px;top:2137px;width:554px;height:122px"><div class="head">How else could this problem be solved?<span class="info-dot">i</span></div><p>Ducimus qui blanditiis praesentium voluptatum pleasure and praising deleniti?</p></div>
  <div class="qcard" style="left:37px;top:2288px;width:554px;height:120px"><div class="head">Who offers these other solutions?<span class="info-dot">i</span></div><p>Ducimus qui blanditiis praesentium voluptatum pleasure and praising deleniti?</p></div>
  <div class="qcard" style="left:37px;top:2439px;width:554px;height:225px"><div class="head">Why is your solution better?<span class="info-dot">i</span></div><p>Ducimus qui blanditiis praesentium voluptatum deleniti atque corrupti quos<br>dolores et quas molestias excepturi sint occaecati ?</p></div>
  <div class="qcard" style="left:609px;top:2439px;width:552px;height:225px"><div class="head">How much does your solution cost?<span class="info-dot">i</span></div><p>Dolores et quas molestias excepturi sint occaecati praesentium voluptatum deleniti atque cupiditate non provident, similique?</p></div>
  <div class="qcard" style="left:37px;top:2693px;width:554px;height:225px"><div class="head">What value are you providing to justify this cost?<span class="info-dot">i</span></div><p>Ducimus qui blanditiis praesentium voluptatum deleniti atque corrupti quos<br>dolores et quas molestias excepturi sint occaecati ?</p></div>
  <div class="qcard" style="left:609px;top:2693px;width:552px;height:225px"><div class="head">How will this make their life/job easier/better?<span class="info-dot">i</span></div><p>Dolores et quas molestias excepturi sint occaecati praesentium voluptatum?</p></div>
  <div class="abs save">SAVE CHANGES</div>
</section>

<footer class="abs footer">
  <div class="copy">Copyrights © 2017 . Leafline | All rights reserved.</div>
  <div class="code">C11</div>
</footer>

</body>
</html>
```